we can communicate on this, but i want to follow the approach we took on Pellew|Marsh & Quinlan but i feel the card front needs the black background and the platinum and gold logo. The back? I am open. we can use the same info from PM&Q. Velmont Arc is an enhanced equity investment fund - basically a very exclusive boutique hedge fund that uses only stock options. very advanced things. hope you are interested

Contact Information for Business Card

Dr. Lewis T. Brennick, CFA
Scientifique de fusée financière
701.555.0143
LTBquant47@mailvantor.com

4718 Willow Creek Bend W.
West Fargo, ND 58078

No web site

Colors

Designer to choose colors to be used in the design.

Requirements
Nice to have
• I tend to prefer the most visible applications of the logo to include logo and name, the logo version with a black background and the gold and platinum components separated by the black. I see this working well for a single side (logo and name - this is card front to me).
• I am fairly open to other treatments on the reverse side with the data. To me, it makes sense to have a different color rendition of the logo on the reverse and it may be a muted black tone on tone or an oversized portion that would have spot UV. Or, the reverse may play with colors and layout
Should not have
• Other colors = no no
• Decorative font

```html
<!DOCTYPE html>
<html lang="en">
<head>
<meta charset="utf-8">
<title>Velmont Arc – Business Card</title>
<link rel="stylesheet" href="https://fonts.googleapis.com/css2?family=Oswald:wght@500&family=Open+Sans:wght@400;600&family=Montserrat:wght@600&display=swap">
<style>
  :root {
    --backdrop: #2b2420;
    --card: #1d1d1d;
    --gold: #d4a72c;
    --white: #ffffff;
    --text-soft: #e6e6e6;
  }
  html, body {
    margin: 0;
    padding: 0;
    width: 1200px;
    height: 1000px;
    overflow: hidden;
    background: var(--backdrop);
  }
  .canvas {
    position: relative;
    width: 1200px;
    height: 1000px;
  }
  .card {
    position: absolute;
    width: 666px;
    height: 396px;
    background: var(--card);
    box-shadow: 0 6px 18px rgba(0,0,0,0.45);
  }
  .card--details { left: 262px; top: 74px; }
  .card--brand { left: 266px; top: 534px; }

  /* Details side */
  .person {
    position: absolute;
    right: 385px;
    top: 166px;
    text-align: right;
  }
  .person__name {
    margin: 0;
    font-family: "Oswald", sans-serif;
    font-weight: 500;
    font-size: 37px;
    line-height: 40px;
    color: var(--gold);
    letter-spacing: 0.5px;
  }
  .person__role {
    margin: 2px 0 0;
    font-family: "Open Sans", sans-serif;
    font-size: 16px;
    color: var(--white);
  }
  .divider {
    position: absolute;
    left: 330px;
    top: 159px;
    width: 2px;
    height: 80px;
    background: var(--text-soft);
  }
  .contact {
    position: absolute;
    left: 376px;
    top: 155px;
    margin: 0;
    padding: 0;
    list-style: none;
    font-family: "Open Sans", sans-serif;
    font-size: 15px;
    color: var(--text-soft);
  }
  .contact__item {
    display: flex;
    align-items: center;
    height: 21px;
  }
  .contact__item:nth-child(2) { margin-top: 3px; }
  .contact__icon {
    width: 12px;
    height: 12px;
    margin-right: 7px;
    fill: var(--gold);
  }
  .address {
    position: absolute;
    left: 60px;
    top: 349px;
    margin: 0;
    font-family: "Open Sans", sans-serif;
    font-size: 15.5px;
    color: var(--text-soft);
    white-space: nowrap;
  }
  .address__company {
    font-weight: 600;
    color: var(--gold);
    text-transform: uppercase;
  }
  .address__bar {
    color: var(--gold);
    margin: 0 8px;
  }

  /* Brand side */
  .brand {
    position: absolute;
    left: 0;
    top: 0;
    width: 100%;
    text-align: center;
  }
  .brand__mark {
    position: absolute;
    left: 259px;
    top: 78px;
    width: 156px;
    height: 156px;
    border-radius: 50%;
    background: var(--gold);
  }
  .brand__name {
    position: absolute;
    left: 0;
    top: 238px;
    width: 100%;
    margin: 0;
    font-family: "Montserrat", sans-serif;
    font-weight: 600;
    color: var(--white);
    text-align: center;
  }
  .brand__primary {
    display: block;
    font-size: 52px;
    line-height: 62px;
    letter-spacing: 1px;
  }
  .brand__secondary {
    display: block;
    font-size: 28px;
    line-height: 36px;
    letter-spacing: 5px;
  }
</style>
</head>
<body>
<main class="canvas">

  <section class="card card--details">
    <div class="person">
      <h1 class="person__name">CARLA FENWICK</h1>
      <p class="person__role">Founder</p>
    </div>
    <div class="divider"></div>
    <ul class="contact">
      <li class="contact__item">
        <svg class="contact__icon" viewBox="0 0 12 12" aria-hidden="true"><path d="M1 3.5C1 2 3 1 6 1s5 1 5 2.5V5H8.5V3.8H3.5V5H1z M2.5 6h7l1 5h-9z"/></svg>
        (000)-000-0000
      </li>
      <li class="contact__item">
        <svg class="contact__icon" viewBox="0 0 12 12" aria-hidden="true"><path d="M3 1h6v3H3z M1 5h10v4H9v2H3V9H1z M4 8v2h4V8z"/></svg>
        (000)-000-0000
      </li>
      <li class="contact__item">
        <svg class="contact__icon" viewBox="0 0 12 12" aria-hidden="true"><path d="M1 2.5h10v7H1z" /><path d="M1.5 3l4.5 3.5L10.5 3" stroke="#1d1d1d" stroke-width="1" fill="none"/></svg>
        info@velmontarc.com
      </li>
      <li class="contact__item">
        <svg class="contact__icon" viewBox="0 0 12 12" aria-hidden="true"><circle cx="6" cy="6" r="5"/><path d="M1 6h10M6 1c-2 2-2 8 0 10M6 1c2 2 2 8 0 10" stroke="#1d1d1d" stroke-width="0.9" fill="none"/></svg>
        www.velmontarc.com
      </li>
    </ul>
    <p class="address">
      <span class="address__company">Velmont Arc</span><span class="address__bar">|</span>212 Harlow Avenue W., Suite 408, Hollis, ON K7P 4R2
    </p>
  </section>

  <section class="card card--brand">
    <div class="brand">
      <div class="brand__mark"></div>
      <h2 class="brand__name">
        <span class="brand__primary">VELMONT</span>
        <span class="brand__secondary">ARC</span>
      </h2>
    </div>
  </section>

</main>
</body>
</html>
```